New business card for a regional office of a US M&A company

We need business card for a finance company, office based in Hong Kong , our Head office is in US, our business is to Merge and acquires companies , the new office will be a regional office for the Asia Pacific region. We want to use the head office logo as attached ( but don't have to be exactly the same, can be a variation to it) as a base and then add Asia Pacific alongside the logo.
We would prefer to have be bilingual Eng + Chinese, although we don't really have Chinese company name .

Industry/Entity Type

Business

Contact Information for Business Card

Clara Jo Tsang
 

VP,
APAC M&A Operations
Orin Vantage Asia Pacific Limited
 
Unit 1407, K18
18 Tai Lok Shan Road, 
Hong Kong 
 
M: +852 6038 1742
T : +852 2836 4100
F : +852 2836 4177
VOIP: 4158
 
cjtsang@orinvantage.com

Font styles to use
Serif
Sans Serif

Colors

Designer to choose colors to be used in the design.

Requirements
Must have
• APAC Office

```html
<!DOCTYPE html>
<html lang="en">
<head>
<meta charset="utf-8">
<title>Orin Vantage Asia Pacific – Business Card</title>
<link rel="stylesheet" href="https://fonts.googleapis.com/css2?family=Montserrat:wght@700&family=Roboto:wght@400;500&display=swap">
<style>
  :root {
    --backdrop: #2b2b2d;
    --card: #1f1f21;
    --accent: #22b9e3;
    --ink: #f2f2f2;
    --ink-soft: #d6d6d6;
    --rule: #8a8a8a;
  }
  * { box-sizing: border-box; margin: 0; padding: 0; }
  html, body { width: 1200px; height: 900px; overflow: hidden; }
  body {
    background: var(--backdrop);
    font-family: "Roboto", Arial, sans-serif;
    color: var(--ink);
    display: flex;
    flex-direction: column;
    align-items: center;
    justify-content: center;
    gap: 48px;
  }
  .card {
    width: 640px;
    height: 366px;
    background: var(--card);
    position: relative;
    box-shadow: 0 10px 28px rgba(0,0,0,.45);
  }

  /* Front */
  .card-front {
    display: flex;
    flex-direction: column;
    align-items: center;
    justify-content: center;
  }
  .brand-mark {
    width: 58px;
    height: 58px;
    background: var(--ink);
    transform: rotate(45deg);
    margin-bottom: 34px;
  }
  .brand-name {
    font-family: "Montserrat", Arial, sans-serif;
    font-weight: 700;
    font-size: 46px;
    letter-spacing: 1px;
    color: var(--accent);
    line-height: 1;
  }
  .web-address {
    margin-top: 34px;
    font-size: 13px;
    letter-spacing: 7px;
    color: var(--ink-soft);
  }

  /* Back */
  .holder {
    position: absolute;
    right: 372px;
    top: 110px;
    text-align: right;
  }
  .holder-name {
    font-size: 24px;
    font-weight: 500;
    color: var(--accent);
    letter-spacing: -0.3px;
  }
  .holder-title {
    margin-top: 6px;
    font-size: 15px;
    font-weight: 500;
    color: var(--ink);
  }
  .divider {
    position: absolute;
    left: 296px;
    top: 100px;
    width: 2px;
    height: 100px;
    background: linear-gradient(to bottom, transparent, var(--rule) 20%, var(--rule) 80%, transparent);
  }
  .contact-list {
    position: absolute;
    left: 320px;
    top: 112px;
    list-style: none;
  }
  .contact-list li {
    display: flex;
    align-items: center;
    gap: 10px;
    font-size: 15px;
    font-weight: 500;
    line-height: 21px;
  }
  .contact-list svg { width: 14px; height: 14px; fill: var(--accent); flex: none; }
  .voip { margin-top: 10px; }
  .office-address {
    position: absolute;
    left: 150px;
    bottom: 46px;
    font-size: 16px;
    line-height: 22px;
    color: var(--ink-soft);
  }
  .office-address .line-1 { padding-left: 14px; }
</style>
</head>
<body>
  <section class="card card-front">
    <div class="brand-mark"></div>
    <div class="brand-name">ORIN VANTAGE</div>
    <div class="web-address">www.orinvantage.com</div>
  </section>

  <section class="card card-back">
    <div class="holder">
      <div class="holder-name">CLARA JO TSANG</div>
      <div class="holder-title">VP</div>
    </div>
    <div class="divider"></div>
    <ul class="contact-list">
      <li>
        <svg viewBox="0 0 24 24" aria-hidden="true"><path d="M6.6 10.8a15.1 15.1 0 0 0 6.6 6.6l2.2-2.2c.3-.3.7-.4 1-.2 1.1.4 2.3.6 3.6.6.6 0 1 .4 1 1V20c0 .6-.4 1-1 1A17 17 0 0 1 3 4c0-.6.4-1 1-1h3.5c.6 0 1 .4 1 1 0 1.3.2 2.5.6 3.6.1.3 0 .7-.2 1z"/></svg>
        +852 2836 4100
      </li>
      <li>
        <svg viewBox="0 0 24 24" aria-hidden="true"><path d="M7 1h10a2 2 0 0 1 2 2v18a2 2 0 0 1-2 2H7a2 2 0 0 1-2-2V3a2 2 0 0 1 2-2zm0 3v14h10V4zm5 15.5a1.2 1.2 0 1 0 0 2.4 1.2 1.2 0 0 0 0-2.4z"/></svg>
        +852 6038 1742
      </li>
      <li>
        <svg viewBox="0 0 24 24" aria-hidden="true"><path d="M6 2h9l3 3v4H6zm-2 8h16a2 2 0 0 1 2 2v8a2 2 0 0 1-2 2H4a2 2 0 0 1-2-2v-8a2 2 0 0 1 2-2zm2 3v2h5v-2zm9 0v2h2v-2zm0 4v2h2v-2z"/></svg>
        +852 2836 4177
      </li>
      <li class="voip">VOIP: 4158</li>
    </ul>
    <address class="office-address">
      <div class="line-1">APAC M&amp;A Operations, Orin Vantage Asia Pacific Limited</div>
      <div>Unit 1407, K18, 18 Tai Lok Shan Road, Hong Kong</div>
    </address>
  </section>
</body>
</html>
```